New business card for a regional office of a US M&A company

We need business card for a finance company, office based in Hong Kong , our Head office is in US, our business is to Merge and acquires companies , the new office will be a regional office for the Asia Pacific region. We want to use the head office logo as attached ( but don't have to be exactly the same, can be a variation to it) as a base and then add Asia Pacific alongside the logo.
We would prefer to have be bilingual Eng + Chinese, although we don't really have Chinese company name .

Industry/Entity Type

Business

Contact Information for Business Card

Clara Jo Tsang
 

VP,
APAC M&A Operations
Orin Vantage Asia Pacific Limited
 
Unit 1407, K18
18 Tai Lok Shan Road, 
Hong Kong 
 
M: +852 6038 1742
T : +852 2836 4100
F : +852 2836 4177
VOIP: 4158
 
cjtsang@orinvantage.com

Font styles to use
Serif
Sans Serif

Colors

Designer to choose colors to be used in the design.

Requirements
Must have
• APAC Office

```html
<!DOCTYPE html>
<html lang="en">
<head>
<meta charset="utf-8">
<title>Orin Vantage Asia Pacific – Business Card</title>
<link rel="stylesheet" href="https://fonts.googleapis.com/css2?family=Ubuntu:wght@400;500;700&display=swap">
<style>
  :root {
    --page-bg: #ededed;
    --navy: #0e2840;
    --navy-deep: #0b2236;
    --sky: #1fa6d0;
    --sky-light: #2cb6dc;
    --sky-dark: #1898c2;
    --silver: #d6dbdf;
    --ink: #0f2a44;
    --white: #ffffff;
  }
  * { box-sizing: border-box; margin: 0; padding: 0; }
  html, body {
    width: 1200px; height: 576px; overflow: hidden;
    background: var(--page-bg);
    font-family: "Ubuntu", sans-serif;
  }
  .canvas { position: relative; width: 1200px; height: 576px; }

  .card {
    position: absolute;
    border-radius: 12px;
    overflow: hidden;
    box-shadow: 0 2px 6px rgba(0,0,0,0.18);
  }

  /* Front */
  .card--front {
    left: 82px; top: 139px; width: 485px; height: 293px;
    background: var(--navy);
  }
  .card--front .edge-band {
    position: absolute; left: 0; right: 0; bottom: 0; height: 6px;
    background: var(--sky);
  }
  .front-mark {
    position: absolute; left: 50%; top: 88px; width: 44px; height: 44px;
    margin-left: -22px; background: var(--silver);
  }
  .front-name {
    position: absolute; left: 0; right: 0; top: 158px;
    text-align: center; font-weight: 700; font-size: 40px; letter-spacing: 0.5px;
    color: var(--sky);
  }

  /* Back */
  .card--back {
    left: 602px; top: 138px; width: 480px; height: 290px;
    background: linear-gradient(180deg, var(--sky-light) 0%, var(--sky) 55%, var(--sky-dark) 100%);
  }
  .card--back .edge-band {
    position: absolute; left: 0; right: 0; bottom: 0; height: 6px;
    background: var(--navy-deep);
  }
  .brand-row {
    position: absolute; left: 16px; top: 38px;
    display: flex; align-items: center; gap: 10px;
  }
  .brand-square { width: 26px; height: 26px; background: var(--silver); }
  .brand-name {
    font-weight: 700; font-size: 27px; letter-spacing: 0.3px; color: var(--ink);
  }
  .person-name {
    position: absolute; left: 18px; top: 113px;
    font-weight: 500; font-size: 18px; color: var(--white);
  }
  .person-title {
    position: absolute; left: 18px; top: 137px;
    font-size: 11.5px; color: var(--ink);
  }
  .company-name {
    position: absolute; left: 18px; top: 170px;
    font-weight: 500; font-size: 13.5px; color: var(--white);
  }
  .contact-list {
    position: absolute; left: 18px; top: 193px; list-style: none;
  }
  .contact-list li {
    display: flex; align-items: center; height: 15.5px;
    font-size: 11.5px; color: var(--ink);
  }
  .contact-icon { width: 9px; height: 9px; margin: 0 11px 0 2px; fill: var(--ink); }
  .address {
    position: absolute; left: 18px; top: 257px;
    font-size: 11.5px; color: var(--ink);
  }
</style>
</head>
<body>
<main class="canvas">

  <section class="card card--front" aria-label="Card front">
    <div class="front-mark"></div>
    <div class="front-name">ORIN VANTAGE</div>
    <div class="edge-band"></div>
  </section>

  <section class="card card--back" aria-label="Card back">
    <div class="brand-row">
      <div class="brand-square"></div>
      <div class="brand-name">ORIN VANTAGE</div>
    </div>

    <div class="person-name">Clara Jo Tsang</div>
    <div class="person-title">Vice President,&nbsp; APAC M&amp;A Operations</div>
    <div class="company-name">Orin Vantage Asia Pacific Limited</div>

    <ul class="contact-list">
      <li>
        <svg class="contact-icon" viewBox="0 0 10 10" aria-label="Mobile"><rect x="2" y="0" width="6" height="10" rx="1"/><rect x="3" y="1.5" width="4" height="6" fill="#2cb6dc"/></svg>
        +852 6038 1742
      </li>
      <li>
        <svg class="contact-icon" viewBox="0 0 10 10" aria-label="Telephone"><path d="M0 3 Q5 0 10 3 L9 5 L7 4 L7 3 Q5 2 3 3 L3 4 L1 5Z"/><rect x="2" y="5" width="6" height="4" rx="1"/></svg>
        +852 2836 4100
      </li>
      <li>
        <svg class="contact-icon" viewBox="0 0 10 10" aria-label="Fax"><rect x="2.5" y="0" width="5" height="3"/><rect x="0" y="3" width="10" height="5" rx="1"/><rect x="2.5" y="7" width="5" height="3"/></svg>
        +852 2836 4177,&nbsp; VOIP: 4158
      </li>
      <li>
        <svg class="contact-icon" viewBox="0 0 10 10" aria-label="Email"><rect x="0" y="2" width="10" height="7"/><path d="M0 2 L5 6 L10 2" fill="none" stroke="#2cb6dc" stroke-width="1"/></svg>
        cjtsang@orinvantage.com
      </li>
    </ul>

    <div class="address">Unit 1407, K18 18, Tai Lok Shan Road, Hong Kong</div>
    <div class="edge-band"></div>
  </section>

</main>
</body>
</html>
```